Weightloss company needs Business Card

We want a business card that is clean and professional, yet portrays that we are a friendly, innovative, and versatile program designed to fit the needs of our clients.
I would like there to be 2 sides, one side having an appointment card, and the other side containing the logo and business information. There can be decorations on both sides. The logo is attached.

Target Market(s)

Men and women 40-60

Industry/Entity Type

Business

Contact Information for Business Card

Font styles to use
Sans Serif

Requirements
Must have
• The logo, space for business information
Nice to have
• The colors in the logo
Should not have
• No pictures of people or food

```html
<!DOCTYPE html>
<html lang="en">
<head>
<meta charset="utf-8">
<title>Turnpoint Wellness – Business Card</title>
<link rel="stylesheet" href="https://fonts.googleapis.com/css2?family=Source+Sans+3:ital,wght@0,400;0,600;0,700;1,400&display=swap">
<style>
  :root {
    --bg: #3d3d3d;
    --card: #ffffff;
    --appt: #fdd3da;
    --red: #e8173a;
    --cyan: #29c6ea;
    --ink: #4a4a4a;
    --rule: #9a9a9a;
  }
  * { box-sizing: border-box; margin: 0; padding: 0; }
  html, body { width: 1105px; height: 1200px; overflow: hidden; }
  body {
    background: var(--bg);
    font-family: "Source Sans 3", Arial, sans-serif;
    position: relative;
  }
  .card {
    position: absolute;
    left: 196px;
    width: 720px;
    border-radius: 22px;
    overflow: hidden;
    box-shadow: 0 6px 14px rgba(0,0,0,.45);
  }
  .card-front { top: 146px; height: 412px; background: var(--card); }
  .card-back  { top: 602px; height: 410px; background: var(--appt); }

  /* front */
  .brand {
    position: absolute; left: 0; right: 0; top: 82px;
    text-align: center;
    color: var(--red);
    font-weight: 700;
    font-size: 40px;
    line-height: 1.02;
    letter-spacing: -0.5px;
  }
  .divider {
    position: absolute; left: 39px; right: 48px; top: 238px;
    height: 2px; background: var(--rule);
  }
  .person { position: absolute; left: 36px; top: 258px; }
  .person-name { color: var(--red); font-size: 26px; font-weight: 600; line-height: 1.1; }
  .person-role { color: var(--cyan); font-size: 19px; line-height: 1.4; margin-bottom: 6px; }
  .person-address { color: var(--ink); font-size: 19px; line-height: 1.42; }

  .contact-list { position: absolute; right: 44px; top: 268px; list-style: none; }
  .contact-item {
    display: flex; justify-content: flex-end; align-items: center;
    color: var(--ink); font-size: 19px; height: 27.5px;
  }
  .contact-item svg { width: 17px; height: 17px; margin-left: 14px; fill: var(--red); flex: none; }

  .color-band { position: absolute; left: 0; right: 0; bottom: 0; height: 12px; display: flex; }
  .color-band .band-red { width: 361px; background: var(--red); }
  .color-band .band-gap { width: 3px; background: var(--card); }
  .color-band .band-cyan { flex: 1; background: var(--cyan); }

  /* back */
  .appt-title {
    position: absolute; left: 0; right: 0; top: 40px;
    text-align: center; color: var(--red); font-size: 28px; font-weight: 600;
  }
  .fill { display: inline-block; border-bottom: 2px dotted #777; height: 1px; vertical-align: baseline; }
  .appt-name-row {
    position: absolute; left: 48px; top: 112px;
    color: var(--ink); font-size: 20px; display: flex; align-items: baseline;
  }
  .appt-name-row .fill { width: 418px; margin-right: 12px; }
  .appt-when-row {
    position: absolute; left: 40px; top: 186px; right: 40px;
    color: var(--red); font-size: 21px; display: flex; align-items: baseline;
  }
  .appt-when-row .fill-date { width: 272px; margin: 0 22px 0 14px; }
  .appt-when-row .fill-time { width: 140px; margin: 0 6px 0 8px; }
  .ampm { font-size: 15px; }
  .day {
    position: absolute; top: 266px;
    color: var(--red); font-size: 19px; display: flex; align-items: center;
  }
  .day .box {
    width: 21px; height: 18px; border: 1.5px solid #555; background: #fff;
    margin-left: 8px;
  }
  .appt-note {
    position: absolute; left: 0; right: 0; top: 340px;
    text-align: center; color: #5a5a5a; font-size: 15px; font-style: italic; line-height: 1.35;
  }
</style>
</head>
<body>

<section class="card card-front" aria-label="Business card front">
  <div class="brand">Turnpoint<br>Wellness</div>
  <div class="divider"></div>

  <div class="person">
    <p class="person-name">DANA WHITFIELD</p>
    <p class="person-role">CEO/FOUNDER</p>
    <p class="person-address">1420 Larkspur Way<br>Fairview, Oregon 97024</p>
  </div>

  <ul class="contact-list">
    <li class="contact-item">555 210 4471
      <svg viewBox="0 0 24 24" aria-hidden="true"><path d="M6.6 10.8a15.1 15.1 0 0 0 6.6 6.6l2.2-2.2c.3-.3.7-.4 1-.2 1.1.4 2.3.6 3.6.6.6 0 1 .4 1 1V20c0 .6-.4 1-1 1A17 17 0 0 1 3 4c0-.6.4-1 1-1h3.5c.6 0 1 .4 1 1 0 1.3.2 2.5.6 3.6.1.3 0 .7-.2 1z"/></svg>
    </li>
    <li class="contact-item">555 318 2096
      <svg viewBox="0 0 24 24" aria-hidden="true"><path d="M7 1h10a2 2 0 0 1 2 2v18a2 2 0 0 1-2 2H7a2 2 0 0 1-2-2V3a2 2 0 0 1 2-2zm0 3v14h10V4zm5 15.2a1 1 0 1 0 0 2 1 1 0 0 0 0-2z"/></svg>
    </li>
    <li class="contact-item">hello@turnpointwell.com
      <svg viewBox="0 0 24 24" aria-hidden="true"><path d="M2 5h20v14H2zm2 2v.4l8 5.2 8-5.2V7zm0 2.8V17h16V9.8l-8 5.2z"/></svg>
    </li>
    <li class="contact-item">www.turnpointwell.com
      <svg viewBox="0 0 24 24" aria-hidden="true"><path d="M12 2a10 10 0 1 0 0 20 10 10 0 0 0 0-20zm-1 17.9A8 8 0 0 1 4.2 10.2L9 15v1a2 2 0 0 0 2 2zm6.9-2.5A2 2 0 0 0 16 16h-1v-3a1 1 0 0 0-1-1H8v-2h2a1 1 0 0 0 1-1V7h2a2 2 0 0 0 2-2v-.4a8 8 0 0 1 2.9 12.8z"/></svg>
    </li>
  </ul>

  <div class="color-band"><span class="band-red"></span><span class="band-gap"></span><span class="band-cyan"></span></div>
</section>

<section class="card card-back" aria-label="Appointment card">
  <h2 class="appt-title">Next Appointment</h2>

  <div class="appt-name-row"><span class="fill"></span>has an apppointment</div>

  <div class="appt-when-row">
    Date :<span class="fill fill-date"></span>
    Time :<span class="fill fill-time"></span><span class="ampm">AM/PM</span>
  </div>

  <div class="day" style="left:46px">Sun<span class="box"></span></div>
  <div class="day" style="left:137px">Mon<span class="box"></span></div>
  <div class="day" style="left:233px">Tue<span class="box"></span></div>
  <div class="day" style="left:337px">Wed<span class="box"></span></div>
  <div class="day" style="left:435px">Thu<span class="box"></span></div>
  <div class="day" style="left:534px">Fri<span class="box"></span></div>
  <div class="day" style="left:610px">Sat<span class="box"></span></div>

  <p class="appt-note">Please give me 24 hours notice if you are unable to keep your appointment or<br>a cancellation fee may be charged.</p>
</section>

</body>
</html>
```